Marwick Law Letterhead

We need a new letterhead design for a Law Firm. The address for the law firm is 1475 Calloway Street, Suite 210, Houston, Texas 77041. Phone Number: 832-361-9027; Fax Number: 832-614-7359. The logo is uploaded to the project.

```html
<!DOCTYPE html>
<html lang="en">
<head>
<meta charset="UTF-8">
<title>Marwick Law Letterhead</title>
<link href="https://fonts.googleapis.com/css2?family=Open+Sans:wght@400;600&family=Lato:wght@400&display=swap" rel="stylesheet">
<style>
  :root {
    --navy: #1b2f63;
    --red: #b0121d;
    --red-dark: #7d0d14;
    --ink: #4a4a4a;
    --paper: #ffffff;
  }
  * { margin: 0; padding: 0; box-sizing: border-box; }
  html, body { width: 1040px; height: 1200px; overflow: hidden; background: var(--paper); }
  .letterhead {
    position: relative; width: 1040px; height: 1200px;
    font-family: "Open Sans", Arial, sans-serif; color: var(--ink);
  }
  .brand-name {
    position: absolute; left: 98px; top: 62px;
    font-size: 40px; font-weight: 600; color: var(--navy); letter-spacing: 0.5px;
  }
  .contact {
    position: absolute; left: 701px; top: 38px;
    border-left: 1px solid #9aa0ad; padding-left: 14px;
    font-size: 17px; color: var(--navy); line-height: 23px;
  }
  .contact-row { display: flex; align-items: center; gap: 8px; }
  .contact-row svg { width: 17px; height: 15px; fill: var(--navy); }
  .letter-body {
    position: absolute; left: 98px; top: 236px; width: 840px;
    font-size: 15px;
  }
  .issue-date { margin-bottom: 17px; }
  .recipient { line-height: 18px; margin-bottom: 50px; }
  .salutation { margin-bottom: 26px; }
  .letter-body p.para { line-height: 27px; text-align: justify; margin-bottom: 27px; }
  .closing { margin-top: 52px; }
  .signature {
    width: 230px; height: 30px; margin: 10px 0 8px;
    background: linear-gradient(90deg, #e6e6e6, #f4f4f4);
  }
  .signer-name { font-size: 18px; color: #333; }
  .signer-title { margin-top: 6px; }
  .footer-wave { position: absolute; left: 0; top: 1030px; width: 1040px; height: 170px; }
  .footer-address {
    position: absolute; right: 119px; top: 1142px;
    font-family: "Lato", Arial, sans-serif; font-size: 18px; color: #fff;
  }
</style>
</head>
<body>
<div class="letterhead">
  <div class="brand-name">Marwick Law</div>

  <div class="contact">
    <div class="contact-row">
      <svg viewBox="0 0 20 18"><path d="M2 6c0-3 4-5 8-5s8 2 8 5l-4 1-1-3H7L6 7 2 6zm3 3h10l2 8H3l2-8z"/></svg>
      <span>832-361-9027</span>
    </div>
    <div class="contact-row">
      <svg viewBox="0 0 20 18"><path d="M5 1h10v5H5zM2 7h16v7h-3v3H5v-3H2zM7 12v3h6v-3z"/></svg>
      <span>832-614-7359</span>
    </div>
  </div>

  <div class="letter-body">
    <div class="issue-date">Issuing Date: May 5, 2018</div>
    <div class="recipient">
      Name Of Employee Mr. XYZABC<br>
      Address of Employee<br>
      Address Line 2 etc..
    </div>
    <div class="salutation">Dear Mr.XYZABC</div>
    <p class="para">Lorem Ipsum has been the industry's standard dummy text ever since the 1500s, when an unknown printer took a galley of type and scrambled it to make a type specimen book. It has survived not only five centuries, but also the leap into electronic typesetting, remaining essentially unchanged. It was popularised in the 1960s with the release of Letraset sheets containing Lorem Ipsum passages, and more recently with desktop publishing software like Aldus PageMaker including versions of Lorem Ipsum.</p>
    <p class="para">Lorem Ipsum is simply dummy text of the printing and typesetting industry. Lorem Ipsum has been the industry's standard dummy text ever since the 1500s, when an unknown printer took a galley of type and scrambled it to make a type specimen book.</p>
    <p class="para">It has survived not only five centuries, but also the leap into electronic typesetting, remaining essentially unchanged. It was popularised in the 1960s with the release of Letraset sheets containing Lorem IpsumIpsum passages.</p>
    <div class="closing">Yours Sincerely</div>
    <div class="signature" role="img" aria-label="Handwritten signature of Daniel Reeves"></div>
    <div class="signer-name">Daniel Reeves</div>
    <div class="signer-title">Managing Director</div>
  </div>

  <svg class="footer-wave" viewBox="0 0 1040 170" preserveAspectRatio="none">
    <defs>
      <linearGradient id="swoosh" x1="0" x2="1" y1="0" y2="0">
        <stop offset="0" stop-color="var(--red)"/>
        <stop offset="1" stop-color="var(--red-dark)"/>
      </linearGradient>
    </defs>
    <path d="M0 60 C200 112 350 108 520 82 S900 22 1040 28 L1040 170 L0 170Z" fill="var(--navy)"/>
    <path d="M0 12 C120 64 300 92 624 50 C350 88 150 86 0 38Z" fill="url(#swoosh)"/>
    <path d="M0 50 C200 104 350 100 520 76 S700 44 640 52" fill="none" stroke="#fff" stroke-width="3"/>
  </svg>
  <div class="footer-address">1475 Calloway Street, Suite 210, Houston, Texas 77041</div>
</div>
</body>
</html>
```